Computer consultant website

Plimvex Software is a newly started computer consulting company. It's a small one-man company that provides mostly Handset applications but also websites in collaboration with designers. I'm running this company on the side of full time university studies.

I'm in need of a website which will function as:
Primarily - I'll direct potential clients to the page so they can read about the company, what i offer and past work.
Secondarily - Making my company visible through the web and maybe getting new clients.

The final design should look modern, clean and professional.

Pages that will be in the final website are (Note that it's not the exact titles as the page will not be in english):
* About
* Services (what Plimvex offers)
* Portfolio/work
* Short news (like ArtHivers "News and press")
* Contact.

Inspiration
http://www.arthiver.example/design/87836
http://www.brookwellstudio.example/
http://www.arthiver.example/design/845881
http://www.arthiver.example/design/1369424 - Lighter design, however a bit cluttered.

No programming code is needed delivered at all. Focus on designing rather then coding.

If you have any questions, do not hesitate to send me a message.

Target Market(s)

Non-technical entrepreneurs and small companies.

Industry/Entity Type

University

Requirements
Must have
• Must have my company logo (see attachment).

Must in any way use both colors from my logo.

A way to logically rearrange content to fit smaller screens. I will implement this design so that it can be pleasantly viewed on mobile devices. You don't necessarily need to provide exactly how the design would look on mobile devices.

I need the following types of page designs:
* Landing page
* Content page
* Portfolio/work (with accompanying inside/clicked) page

Landing/start page must in any way include at least the information:
* Shorter version of "About Plimvex"
* At least 1 most recent portfolio/work entry
* At least 1 most recent news entry
* Services that Plimvex offers.
Nice to have
• -
Should not have
• Testimonials or newsletter.

```html
<!DOCTYPE html>
<html lang="en">
<head>
<meta charset="utf-8">
<title>Plimvex Software</title>
<link rel="stylesheet" href="https://fonts.googleapis.com/css2?family=Yanone+Kaffeesatz:wght@400;600;700&family=Source+Sans+3:wght@300;400;600&display=swap">
<style>
  :root {
    --blue: #1c74e6;
    --blue-light: #5cb2f6;
    --blue-deep: #1459c9;
    --sky: #1f93d9;
    --ink: #2f2f31;
    --grey: #6b6b6b;
    --page: #f6f6f6;
    --band: #e9e9e9;
    --frame: #e2e2e2;
    --foot: #3b3b3b;
    --foot-deep: #1f1f1f;
    --field: #101010;
    --white: #ffffff;
  }
  * { box-sizing: border-box; margin: 0; padding: 0; }
  html, body { width: 967px; height: 1200px; overflow: hidden; }
  body {
    position: relative;
    background: var(--page);
    font-family: "Source Sans 3", sans-serif;
    color: var(--grey);
  }
  h1, h2, h3, h4 { font-weight: 400; }
  .abs { position: absolute; }
  .top-band {
    left: 0; top: 0; width: 967px; height: 360px;
    background: linear-gradient(#f2f2f2, var(--band));
  }
  .head-font { font-family: "Yanone Kaffeesatz", sans-serif; }

  /* header */
  .brand { left: 90px; top: 15px; display: flex; align-items: center; gap: 18px; }
  .brand-mark { width: 82px; height: 82px; border-radius: 50%; background: var(--blue); }
  .brand-name { font-family: "Source Sans 3", sans-serif; font-weight: 600; font-size: 60px; color: var(--ink); line-height: 1; }
  .search { left: 668px; top: 42px; width: 215px; height: 29px; background: #ececec; border: 1px solid #e0e0e0; }
  .search span { position: absolute; left: 8px; top: 6px; font-size: 11.5px; color: #555; }
  .search-btn { position: absolute; right: -1px; top: -1px; width: 29px; height: 29px; background: #2a2a2a; }
  .main-nav { left: 0; top: 128px; }
  .main-nav a { position: absolute; font-size: 14.5px; font-weight: 300; color: #444; text-decoration: none; white-space: nowrap; }
  .main-nav a.is-active { color: var(--blue); }
  .nav-underline { left: 97px; top: 151px; width: 50px; height: 3px; background: var(--blue); }
  .talk { right: 84px; top: 101px; text-align: right; }
  .talk-lead { font-size: 25px; color: #777; line-height: 1.1; }
  .talk-phone { font-size: 27px; font-weight: 700; color: var(--blue); line-height: 1.05; white-space: nowrap; }

  /* hero */
  .hero-frame { left: 71px; top: 166px; width: 825px; height: 305px; background: var(--frame); border-radius: 4px; }
  .hero { left: 78px; top: 174px; width: 810px; height: 289px; border-radius: 6px;
    background: radial-gradient(ellipse at 30% 45%, var(--blue-light), #2d86ee 55%, var(--blue-deep)); overflow: hidden; }
  .hero-photo { left: 78px; top: 20px; width: 222px; height: 269px; border-radius: 14px 14px 0 0;
    background: linear-gradient(160deg, #2b2b2b, #111 60%, #d4a98a 100%); }
  .hero-title { left: 367px; top: 60px; font-size: 40px; color: var(--white); }
  .hero-text { left: 369px; top: 113px; width: 322px; font-size: 10.6px; line-height: 17px; color: var(--white); }
  .btn { display: flex; align-items: center; justify-content: center; background: linear-gradient(#2a8cf4, var(--blue-deep));
    color: var(--white); border-radius: 5px; font-family: "Yanone Kaffeesatz", sans-serif; box-shadow: 0 3px 6px rgba(0,0,0,.18); }
  .hero-cta { left: 368px; top: 178px; width: 121px; height: 29px; font-size: 21px; }
  .hero-arrow { width: 30px; height: 30px; border-radius: 50%; background: #2d2d2d; opacity: .9; }

  /* intro columns */
  .intro-title { font-size: 26px; color: var(--blue); text-transform: uppercase; top: 481px; white-space: nowrap; }
  .intro-icon { width: 42px; height: 42px; border-radius: 50%; background: linear-gradient(#3c9cf6, var(--blue)); border: 2px solid #d9e8fb; top: 478px; }
  .intro-text { width: 230px; font-size: 11.2px; line-height: 20px; color: var(--grey); top: 519px; }
  .read-more { width: 80px; height: 29px; font-size: 17px; }
  .divider { width: 1px; top: 478px; height: 150px; background: linear-gradient(transparent, #dadada, transparent); }

  /* services */
  .services-title { left: 0; width: 967px; top: 643px; text-align: center; font-size: 21px; color: var(--sky); }
  .card { width: 195px; height: 134px; top: 682px; background: var(--white); border: 1px solid #dcdcdc; padding: 8px; box-shadow: 0 4px 6px rgba(0,0,0,.06); }
  .card-art { width: 100%; height: 100%; }
  .service-name { font-size: 15.5px; font-weight: 400; color: var(--sky); top: 834px; }
  .service-text { width: 190px; font-size: 9.4px; line-height: 15px; color: #444; top: 857px; }
  .mini-arrow { width: 16px; height: 16px; border-radius: 50%; background: #333; top: 683px; }

  /* footer */
  .footer { left: 0; top: 1007px; width: 967px; height: 193px; background: linear-gradient(var(--foot), #2b2b2b); }
  .footer-base { left: 0; top: 1160px; width: 967px; height: 40px; background: var(--foot-deep); }
  .up-btn { left: 469px; top: 990px; width: 30px; height: 30px; border-radius: 50%; background: var(--foot); }
  .foot-title { font-size: 22px; color: #e6e6e6; top: 1012px; font-weight: 400; }
  .quick-links { left: 90px; top: 1047px; list-style: none; }
  .quick-links li { font-size: 12.8px; line-height: 18.5px; color: #e4e4e4; }
  .social-dot { width: 38px; height: 38px; border-radius: 50%; }
  .social-main { font-size: 17px; color: #e8e8e8; white-space: nowrap; }
  .social-sub { font-size: 12.5px; color: #e0e0e0; white-space: nowrap; }
  .field { background: var(--field); border-radius: 5px; color: #888; font-size: 9px; padding: 9px 12px; font-family: "Yanone Kaffeesatz", sans-serif; letter-spacing: .5px; }
  .submit { left: 768px; top: 1084px; width: 79px; height: 29px; font-size: 16px; }
  .copyright { right: 91px; top: 1174px; font-size: 10.5px; color: #c9c9c9; white-space: nowrap; }
</style>
</head>
<body>
  <div class="abs top-band"></div>

  <header>
    <div class="abs brand">
      <span class="brand-mark"></span>
      <span class="brand-name">plimvex</span>
    </div>
    <div class="abs search">
      <span>Search</span>
      <div class="search-btn">
        <svg width="29" height="29" viewBox="0 0 29 29"><circle cx="16" cy="12" r="5" fill="none" stroke="#fff" stroke-width="2"/><line x1="12.5" y1="15.5" x2="7" y2="21" stroke="#fff" stroke-width="2.5" stroke-linecap="round"/></svg>
      </div>
    </div>
    <nav class="abs main-nav">
      <a class="is-active" style="left:102px">Home</a>
      <a style="left:180px">About</a>
      <a style="left:257px">Services</a>
      <a style="left:346px">Portfolio</a>
      <a style="left:436px">News</a>
      <a style="left:510px">Contact us</a>
    </nav>
    <div class="abs nav-underline"></div>
    <div class="abs talk head-font">
      <div class="talk-lead">Want to Talk?</div>
      <div class="talk-phone">1800-555-0142</div>
    </div>
  </header>

  <section>
    <div class="abs hero-frame"></div>
    <div class="abs hero">
      <div class="abs hero-photo" role="img" aria-label="Hand holding a tablet showing an app home screen"></div>
      <h1 class="abs hero-title head-font">Handset Apps.</h1>
      <p class="abs hero-text">Praesent pellentesque ullamcorper nulla, et molestie justo dapibus non. Phasellus tempor dapibus varius. Nulla facilisi. Vivamus pulvinar dapibus laoreet.</p>
      <div class="abs btn hero-cta">Get it Now</div>
    </div>
    <div class="abs hero-arrow" style="left:98px;top:303px">
      <svg width="30" height="30" viewBox="0 0 30 30"><path d="M17 9l-6 6 6 6" fill="none" stroke="#fff" stroke-width="1.5"/></svg>
    </div>
    <div class="abs hero-arrow" style="left:836px;top:303px">
      <svg width="30" height="30" viewBox="0 0 30 30"><path d="M13 9l6 6-6 6" fill="none" stroke="#fff" stroke-width="1.5"/></svg>
    </div>
  </section>

  <section>
    <h2 class="abs intro-title head-font" style="left:92px">About Plimvex</h2>
    <div class="abs intro-icon" style="left:283px">
      <svg width="38" height="38" viewBox="0 0 38 38"><path d="M16 27v-9a2 2 0 0 1 4 0v4l5 1.5a2 2 0 0 1 1.5 2.2L26 29h-9z" fill="none" stroke="#fff" stroke-width="1.6"/><path d="M14 14a5 5 0 0 1 8 0" fill="none" stroke="#fff" stroke-width="1.4"/></svg>
    </div>
    <p class="abs intro-text" style="left:91px">Sed ut perspiciatis unde omnis iste natus error sit voluptatem accusantium doloremque lau-dantium, totam rem aperiam,</p>
    <div class="abs btn read-more" style="left:88px;top:587px">READ MORE</div>

    <div class="abs divider" style="left:341px"></div>

    <h2 class="abs intro-title head-font" style="left:373px">Most Recent Job</h2>
    <div class="abs intro-icon" style="left:560px">
      <svg width="38" height="38" viewBox="0 0 38 38"><rect x="14" y="12" width="11" height="14" fill="none" stroke="#fff" stroke-width="1.6"/><line x1="16.5" y1="16" x2="22.5" y2="16" stroke="#fff"/><line x1="16.5" y1="19" x2="22.5" y2="19" stroke="#fff"/><line x1="16.5" y1="22" x2="22.5" y2="22" stroke="#fff"/></svg>
    </div>
    <p class="abs intro-text" style="left:369px">Sed ut perspiciatis unde omnis iste natus error sit voluptatem accusantium doloremque lau-dantium, totam rem aperiam,</p>
    <div class="abs btn read-more" style="left:367px;top:587px">READ MORE</div>

    <div class="abs divider" style="left:624px"></div>

    <h2 class="abs intro-title head-font" style="left:652px">Most Recent News</h2>
    <div class="abs intro-icon" style="left:842px">
      <svg width="38" height="38" viewBox="0 0 38 38"><rect x="12" y="12" width="14" height="9" fill="#fff"/><line x1="19" y1="21" x2="19" y2="27" stroke="#fff" stroke-width="2"/></svg>
    </div>
    <p class="abs intro-text" style="left:656px">Sed ut perspiciatis unde omnis iste natus error sit voluptatem accusantium doloremque lau-dantium, totam rem aperiam,</p>
    <div class="abs btn read-more" style="left:654px;top:587px">READ MORE</div>
  </section>

  <section>
    <h2 class="abs services-title head-font">SERVICES THAT PLIMVEX OFFERS</h2>

    <div class="abs card" style="left:81px">
      <div class="card-art" role="img" aria-label="Dark close-up of design work with a zoom button" style="background:linear-gradient(135deg,#4a4543,#2a2727);position:relative">
        <svg class="abs" style="left:68px;top:25px" width="42" height="42" viewBox="0 0 42 42"><circle cx="21" cy="21" r="20" fill="#bdbdbd" opacity=".8"/><path d="M21 13v16M13 21h16" stroke="#444" stroke-width="3"/></svg>
      </div>
    </div>
    <div class="abs card" style="left:285px">
      <div class="card-art" role="img" aria-label="Tablet and phone showing a photo gallery app" style="background:linear-gradient(90deg,#fff 5%,#222 10%,#8a9aa8 35%,#222 55%,#fff 62%,#fff 70%,#222 72%,#a6b0a0 85%,#222 90%,#fff 95%)"></div>
    </div>
    <div class="abs card" style="left:489px">
      <div class="card-art" role="img" aria-label="Colourful tree of app icons" style="background:radial-gradient(circle at 50% 45%,#e9c9a0,#f5f0ee 45%,#fff 70%)"></div>
    </div>
    <div class="abs card" style="left:694px">
      <div class="card-art" role="img" aria-label="Phone with envelopes and an at sign" style="background:linear-gradient(160deg,#bdbdbd 40%,#fff 41%,#f1d6d6 70%,#c7c7c7)"></div>
    </div>
    <div class="abs mini-arrow" style="left:850px"><svg width="16" height="16" viewBox="0 0 16 16"><path d="M9.5 5l-3 3 3 3" fill="none" stroke="#fff"/></svg></div>
    <div class="abs mini-arrow" style="left:871px"><svg width="16" height="16" viewBox="0 0 16 16"><path d="M6.5 5l3 3-3 3" fill="none" stroke="#fff"/></svg></div>

    <h3 class="abs service-name" style="left:89px">Web Design</h3>
    <p class="abs service-text" style="left:90px">Lorem ipsum dolor sit amet, consectetu adipiscing elit, sed diam nonummy nibh euismod tincidunt ut laoreet iam.</p>
    <div class="abs btn read-more" style="left:84px;top:940px">READ MORE</div>

    <h3 class="abs service-name" style="left:294px">Handset Apps</h3>
    <p class="abs service-text" style="left:294px">Lorem ipsum dolor sit amet, consectetu adipiscing elit, sed diam nonummy nibh euismod tincidunt ut laoreet iam.</p>
    <div class="abs btn read-more" style="left:289px;top:940px">READ MORE</div>

    <h3 class="abs service-name" style="left:498px">Mobile Apps</h3>
    <p class="abs service-text" style="left:498px">Lorem ipsum dolor sit amet, consectetu adipiscing elit, sed diam nonummy nibh euismod tincidunt ut laoreet iam.</p>
    <div class="abs btn read-more" style="left:493px;top:940px">READ MORE</div>

    <h3 class="abs service-name" style="left:702px">Email</h3>
    <p class="abs service-text" style="left:702px">Lorem ipsum dolor sit amet, consectetu adipiscing elit, sed diam nonummy nibh euismod tincidunt ut laoreet iam.</p>
    <div class="abs btn read-more" style="left:697px;top:940px">READ MORE</div>
  </section>

  <footer>
    <div class="abs footer"></div>
    <div class="abs footer-base"></div>
    <div class="abs up-btn"><svg width="30" height="30" viewBox="0 0 30 30"><path d="M10 17l5-5 5 5" fill="none" stroke="#ddd" stroke-width="1.4"/></svg></div>

    <h4 class="abs foot-title head-font" style="left:88px">Quick Links</h4>
    <ul class="abs quick-links">
      <li>Home</li><li>About</li><li>Services</li><li>Portfolio</li><li>News</li><li>Contact Us</li>
    </ul>

    <h4 class="abs foot-title head-font" style="left:306px;top:1014px">Follow Us</h4>
    <div class="abs social-dot" style="left:299px;top:1051px;background:#d8372b"></div>
    <div class="abs social-main head-font" style="left:348px;top:1050px">We are on Circlenet</div>
    <div class="abs social-sub head-font" style="left:349px;top:1073px">Add to your circle</div>
    <div class="abs social-dot" style="left:299px;top:1104px;background:#27a2e4"></div>
    <div class="abs social-main head-font" style="left:345px;top:1103px">We are on Chirpline</div>
    <div class="abs social-sub head-font" style="left:345px;top:1124px">Follow me</div>

    <h4 class="abs foot-title head-font" style="left:555px;top:1017px">Contact Us</h4>
    <div class="abs field" style="left:550px;top:1051px;width:102px;height:26px">NAME</div>
    <div class="abs field" style="left:659px;top:1051px;width:102px;height:26px">EMAIL</div>
    <div class="abs field" style="left:550px;top:1083px;width:211px;height:32px">MESSAGE</div>
    <div class="abs btn submit">SUBMIT</div>

    <p class="abs copyright">Copyright &nbsp;©&nbsp; 2103 &nbsp;www.plimvex.example &nbsp;&nbsp; All rights reserved.</p>
  </footer>
</body>
</html>
```